Torvane Halbridge

Looking for modern business cards.
Clean contemporary design.
Similar to this.
https://www.plumvexa-search.example/imgres?imgurl=https%3A%2F%2Fimg.quorlint-cdn.example%2Fsleek_dark_metal_card_design_540.jpg&imgrefurl=https%3A%2F%2Fwww.quorlint-prints.example%2Fsleek_dark_metal_card_design-918273645501928374&q=modern%20business%20cards

But I'd like the blue to look metallic.

Business

```html
<!DOCTYPE html>
<html lang="en">
<head>
<meta charset="utf-8">
<title>Torvane Halbridge — Business Card</title>
<link rel="stylesheet" href="https://fonts.googleapis.com/css2?family=Roboto:ital,wght@0,400;0,500;0,700;1,500&family=Roboto+Condensed:wght@500;700&display=swap">
<style>
  :root {
    --stage: #e4e4e4;
    --paper: #f6f6f6;
    --navy: #235770;
    --navy-light: #2c6a86;
    --navy-dark: #1c4a60;
    --teal: #2a9bc1;
    --ink: #4a4a4a;
    --rule: #8a8a8a;
  }
  * { box-sizing: border-box; margin: 0; padding: 0; }
  html, body { width: 1200px; height: 960px; overflow: hidden; }
  body {
    position: relative;
    background: var(--stage);
    font-family: "Roboto", Arial, sans-serif;
  }
  .card {
    position: absolute;
    width: 601px;
    height: 343px;
  }
  .card--front { left: 314px; top: 113px; background: var(--paper); }
  .card--back {
    left: 311px; top: 472px;
    background: linear-gradient(135deg, var(--navy-dark) 0%, var(--navy) 35%, var(--navy-light) 55%, var(--navy) 75%, var(--navy-dark) 100%);
  }

  .brand { position: absolute; display: flex; align-items: center; gap: 8px; }
  .brand__name { font-weight: 500; letter-spacing: -0.5px; white-space: nowrap; }
  .brand__dot { border-radius: 50%; background: var(--teal); flex: none; }
  .tagline { position: absolute; font-style: italic; font-weight: 500; color: var(--teal); white-space: nowrap; letter-spacing: 0.6px; }

  .card--front .brand { left: 39px; top: 66px; }
  .card--front .brand__name { font-size: 27px; color: var(--navy); }
  .card--front .brand__dot { width: 9px; height: 9px; }
  .card--front .tagline { left: 96px; top: 99px; font-size: 6px; }

  .holder { position: absolute; right: 38px; top: 149px; text-align: right; }
  .holder__name { font-family: "Roboto Condensed", Arial, sans-serif; font-weight: 700; font-size: 21px; color: var(--navy); line-height: 24px; }
  .holder__title { font-family: "Roboto Condensed", Arial, sans-serif; font-weight: 500; font-size: 15px; color: var(--teal); line-height: 20px; }
  .edge-tab { position: absolute; right: 1px; top: 150px; width: 14px; height: 40px; background: var(--navy); }

  .divider { position: absolute; left: 39px; top: 202px; width: 520px; height: 1px; background: var(--rule); }

  .contacts { position: absolute; left: 39px; top: 216px; list-style: none; }
  .contacts li { display: flex; align-items: center; gap: 8px; height: 19px; font-size: 14px; color: var(--ink); }
  .contacts svg { width: 14px; height: 14px; fill: var(--navy); flex: none; }

  .address { position: absolute; right: 38px; top: 278px; text-align: right; font-size: 14px; line-height: 19px; color: var(--ink); font-style: normal; }

  .card--back .brand { left: 151px; top: 158px; }
  .card--back .brand__name { font-size: 36px; color: #ffffff; }
  .card--back .brand__dot { width: 11px; height: 11px; }
  .card--back .tagline { left: 230px; top: 202px; font-size: 7px; }
  .site { position: absolute; left: 0; right: 0; top: 288px; text-align: center; font-size: 15px; letter-spacing: 3px; color: #ffffff; }
</style>
</head>
<body>
  <section class="card card--front" aria-label="Card front">
    <div class="brand">
      <span class="brand__name">Torvane Halbridge</span>
      <span class="brand__dot"></span>
    </div>
    <p class="tagline">"Steady counsel for companies ready to grow"</p>

    <div class="holder">
      <p class="holder__name">DORIAN KESSEL</p>
      <p class="holder__title">CEO/FOUNDER</p>
    </div>
    <span class="edge-tab"></span>

    <div class="divider"></div>

    <ul class="contacts">
      <li><svg viewBox="0 0 24 24"><path d="M6.6 10.8a15.1 15.1 0 0 0 6.6 6.6l2.2-2.2c.3-.3.7-.4 1-.2 1.1.4 2.3.6 3.6.6.6 0 1 .4 1 1V20c0 .6-.4 1-1 1A17 17 0 0 1 3 4c0-.6.4-1 1-1h3.5c.6 0 1 .4 1 1 0 1.3.2 2.5.6 3.6.1.3 0 .7-.2 1z"/></svg>612 574 3081</li>
      <li><svg viewBox="0 0 24 24"><path d="M16 1H8a2 2 0 0 0-2 2v18a2 2 0 0 0 2 2h8a2 2 0 0 0 2-2V3a2 2 0 0 0-2-2zm0 17H8V4h8zm-4 4a1 1 0 1 1 0-2 1 1 0 0 1 0 2z"/></svg>847 203 6159</li>
      <li><svg viewBox="0 0 24 24"><path d="M19 8H5a3 3 0 0 0-3 3v6h4v4h12v-4h4v-6a3 3 0 0 0-3-3zm-3 11H8v-5h8zM18 3H6v4h12z"/></svg>493 718 2065</li>
      <li><svg viewBox="0 0 24 24"><path d="M2 5h20v14H2zm2 2v.5l8 5 8-5V7zm0 3v7h16v-7l-8 5z"/></svg>dorian@halbridge.example</li>
      <li><svg viewBox="0 0 24 24"><path d="M12 2a10 10 0 1 0 0 20 10 10 0 0 0 0-20zm-1 17.9A8 8 0 0 1 4.2 10.2L9 15v1a2 2 0 0 0 2 2zm6.9-2.5A2 2 0 0 0 16 16h-1v-3a1 1 0 0 0-1-1H8v-2h2a1 1 0 0 0 1-1V7h2a2 2 0 0 0 2-2v-.4a8 8 0 0 1 2.9 12.8z"/></svg>www.halbridge.example</li>
    </ul>

    <address class="address">4210 Larkspur Way<br>Fenmoor, Alaska 34118</address>
  </section>

  <section class="card card--back" aria-label="Card back">
    <div class="brand">
      <span class="brand__name">Torvane Halbridge</span>
      <span class="brand__dot"></span>
    </div>
    <p class="tagline">"Steady counsel for companies ready to grow"</p>
    <p class="site">www.torvanehalbridge.example</p>
  </section>
</body>
</html>
```